We’re a real estate firm that has landed a big builder in a neighboring state. Our branding needs...

We are a real estate firm who represents various builders along with doing resale here in Oregon. Our firm is growing to represent a big builder in Washington State and we’ll have another 40 brokers on our team. We need rebranding. As in, a new logo ( the house logo we have now looks cartoonish, hate it). We need new cards, something to really stand out. I’ve been thinking of using those NFC cards from ZEP or the ones with the seam color. I likely want two or three designs, a darker (as in a background color of black or grey) , a light one ( again I mean background color) and a credit card style (either plastic w an embossed name/number on front, or metal ). I’m thinking dark background for cc, or silver if it’s metal. That’s my thoughts, but you are the artists, so maybe you have an idea I haven’t considered. Our colors were black and red, but we don’t have to stick to that. Just nothing too busy. Oh, and we are typically representing the local, higher quality builders in our area (just below custom), but not national. Subdivisions are near the Kell Varney, Brisco, and Thornfield Crest sites. We are super excited, but without a lot of time to change the “look” of our brokerage. So I’ll be deciding and moving forward within 24 hours tops. Our name is Real Estate Summit Alliance ( we cant change the name because of timeline and business license) Thank you!

Industry/Entity Type

Real Estate

Contact Information for Business Card

The usual. Name of firm. Name of cardholder. Contact info.

Font styles to use
Serif
Sans Serif

Colors

Designer to choose colors to be used in the design.

Requirements
Must have
• A sleek or simple look. I included photos of cards with stylistic attributes we like. Thank you
Nice to have
• We really like the black backgrounds. With foil or embossed detail. We also like the black on black. Matte black card with raised shiny black detail. But still eye catching.
Should not have
• No ornate or busy looking style. We don’t want anything cluttered.

```html
<!DOCTYPE html>
<html lang="en">
<head>
<meta charset="utf-8">
<title>Real Estate Summit Alliance – Business Cards</title>
<link rel="stylesheet" href="https://fonts.googleapis.com/css2?family=Open+Sans:wght@400;600;700&display=swap">
<style>
  :root {
    --stage: #141414;
    --card: #1e1e1f;
    --card-edge: #2a2a2b;
    --panel-top: #2b2b2c;
    --panel-bottom: #202021;
    --red: #d3161d;
    --silver: #c9c9cb;
    --white: #f2f2f2;
    --muted: #a9a9ab;
    --rule: #4a4a4c;
  }
  * { box-sizing: border-box; margin: 0; padding: 0; }
  html, body { width: 1200px; height: 900px; overflow: hidden; }
  body {
    background: var(--stage);
    font-family: "Open Sans", Arial, sans-serif;
    position: relative;
  }
  .card {
    position: absolute;
    left: 290px;
    width: 620px;
    height: 354px;
    border-radius: 22px;
    background: var(--card);
    border: 1px solid var(--card-edge);
    box-shadow: 0 18px 40px rgba(0,0,0,.6);
    overflow: hidden;
  }
  .card--back { top: 68px; }
  .card--front { top: 478px; }

  .decor-panel {
    position: absolute;
    left: 0; top: 0;
    width: 250px; height: 100%;
    background: linear-gradient(180deg, var(--panel-top), var(--panel-bottom));
    opacity: .55;
  }

  /* back */
  .back-brand {
    position: absolute;
    left: 230px; top: 90px;
    width: 340px;
    color: var(--silver);
    font-weight: 700;
    font-size: 36px;
    line-height: 1.12;
    text-transform: uppercase;
    letter-spacing: .5px;
  }
  .back-web {
    position: absolute;
    left: 230px; top: 250px;
    color: var(--white);
    font-size: 15px;
  }

  /* front */
  .front-brand {
    position: absolute;
    right: 36px; top: 34px;
    width: 330px;
    text-align: right;
    color: var(--red);
    font-weight: 700;
    font-size: 28px;
    line-height: 1.12;
    text-transform: uppercase;
  }
  .front-rule {
    position: absolute;
    left: 220px; right: 28px; top: 148px;
    height: 1px;
    background: var(--rule);
  }
  .address {
    position: absolute;
    right: 36px; top: 164px;
    text-align: right;
    color: var(--muted);
    font-size: 16px;
    line-height: 1.3;
  }
  .holder {
    position: absolute;
    left: 36px; bottom: 26px;
  }
  .holder-name {
    color: var(--red);
    font-weight: 700;
    font-size: 19px;
    text-transform: uppercase;
    letter-spacing: .3px;
  }
  .holder-role {
    color: var(--white);
    font-size: 17px;
    margin-bottom: 8px;
  }
  .contact-list { list-style: none; }
  .contact-list li {
    display: flex;
    align-items: center;
    gap: 8px;
    color: var(--muted);
    font-size: 17px;
    line-height: 1.3;
  }
  .contact-list svg { width: 13px; height: 13px; fill: var(--red); flex: none; }
</style>
</head>
<body>

<section class="card card--back">
  <div class="decor-panel" role="img" aria-label="Faint tone-on-tone house silhouette decoration"></div>
  <div class="back-brand">Real Estate<br>Summit Alliance</div>
  <div class="back-web">www.summitalliance-re.com</div>
</section>

<section class="card card--front">
  <div class="decor-panel" role="img" aria-label="Faint tone-on-tone house silhouette decoration"></div>
  <div class="front-brand">Real Estate<br>Summit Alliance</div>
  <div class="front-rule"></div>
  <address class="address" style="font-style:normal">
    4820 Cedar Ridge Lane<br>Portland, OR 97205
  </address>
  <div class="holder">
    <div class="holder-name">Marcus Hale</div>
    <div class="holder-role">Managing Director</div>
    <ul class="contact-list">
      <li>
        <svg viewBox="0 0 16 16" aria-hidden="true"><path d="M3 1h3l1.5 4-2 1.3a9 9 0 0 0 4.2 4.2L11 8.5l4 1.5v3a2 2 0 0 1-2 2A12 12 0 0 1 1 3a2 2 0 0 1 2-2z"/></svg>
        503-555 014 221
      </li>
      <li>
        <svg viewBox="0 0 16 16" aria-hidden="true"><path d="M4.5 0h7A1.5 1.5 0 0 1 13 1.5v13a1.5 1.5 0 0 1-1.5 1.5h-7A1.5 1.5 0 0 1 3 14.5v-13A1.5 1.5 0 0 1 4.5 0zM5 2v10h6V2zm3 11a1 1 0 1 0 0 2 1 1 0 0 0 0-2z"/></svg>
        503-555 014 221
      </li>
      <li>
        <svg viewBox="0 0 16 16" aria-hidden="true"><path d="M1 3h14v1.2L8 9 1 4.2zm0 2.6 7 4.8 7-4.8V13H1z"/></svg>
        hello@summitalliance-re.com
      </li>
    </ul>
  </div>
</section>

</body>
</html>
```